Logo with Stationery Design Project-

The company is an on-line service for assisting the people that are in a foreclosure situation with their homes. We are presently building the site on WebMarlin with Wordpress.

The best option to save a home in the USA at the end of the line with the banks is to file for bankruptcy Chapter 7 or Chapter 13. We work with homeowners and attorneys to prepare the financial package for the attorneys to negotiate with the banks after filing for bankruptcy. We also sell a binder on-line which is called the northgate renewal set and the web site is: www.northgaterenewalset.example
We need a logo and stationnary to communicate the message of advisors in the field of financial strategies when it comes to the foreclosure and bankruptcy process. This stationnary will be printed on high quality paper with the business cards being on 100 stock which is high quality in the USA.

We would like to see the logo to use the Navy blue and Aqua Green colors. The final desing should communicate the financial knowledge and promise of a light at the end of the tunnell.

The card should use both sides with the back side being the logo and the web site address that links with the front of the card. Letterhead and envelopes should be serious but sexy!

A challenge that I am sure someone is up to........

Target Market(s)

12 million people that are in foreclosure in the USA and all of the law firms that deal with foreclosure and bankruptcies in the USA all 50 states

Industry/Entity Type

Financial

Requirements
Must have
• Colors are important = Navy blue and Aqua green

```html
<!DOCTYPE html>
<html lang="en">
<head>
<meta charset="utf-8">
<title>Northgate Renewal – Stationery</title>
<link rel="stylesheet" href="https://fonts.googleapis.com/css2?family=Questrial&family=Open+Sans:wght@400;600;700&display=swap">
<style>
  :root {
    --navy: #1e2f55;
    --aqua: #12ad98;
    --folder: #0fb09b;
    --paper: #ffffff;
    --ink: #3a3a3a;
    --backdrop: #3b3c3e;
  }
  * { box-sizing: border-box; margin: 0; padding: 0; }
  html, body { width: 1200px; height: 1000px; overflow: hidden; }
  body { background: var(--backdrop); position: relative; font-family: "Open Sans", sans-serif; }

  .brand { display: flex; align-items: center; gap: 10px; font-family: "Questrial", sans-serif; line-height: 1; white-space: nowrap; }
  .brand__square { flex: none; }

  .url { position: absolute; font-family: "Questrial", sans-serif; letter-spacing: 0.5px; white-space: nowrap; }
  .url .url__accent { color: var(--aqua); }

  /* Presentation folder */
  .folder { position: absolute; left: 108px; top: 40px; width: 440px; height: 620px; background: var(--folder); }
  .folder .brand { position: absolute; left: 0; right: 0; top: 370px; justify-content: center; color: #fff; font-size: 36px; }
  .folder .brand__square { width: 30px; height: 30px; background: #fff; }
  .folder .url { left: 0; right: 0; bottom: 28px; text-align: center; color: #fff; font-size: 15px; }
  .folder .url .url__accent { color: var(--navy); }

  /* Letterhead */
  .letterhead { position: absolute; left: 658px; top: 40px; width: 440px; height: 620px; background: var(--paper); color: var(--ink); }
  .letterhead .brand { position: absolute; left: 22px; top: 62px; color: var(--navy); font-size: 18px; gap: 7px; }
  .letterhead .brand__square { width: 14px; height: 14px; background: var(--aqua); }
  .sender { position: absolute; left: 23px; top: 89px; font-size: 7.5px; font-weight: 700; color: #222; line-height: 10px; }
  .contact-line { display: flex; align-items: center; gap: 4px; }
  .contact-line svg { flex: none; }
  .recipient { position: absolute; right: 12px; top: 133px; text-align: right; font-size: 6.5px; line-height: 9px; }
  .letter-body { position: absolute; left: 32px; right: 12px; top: 169px; font-size: 6.5px; line-height: 9px; }
  .letter-body p { margin-bottom: 9px; }
  .letterhead .url { left: 0; right: 0; bottom: 12px; text-align: center; font-size: 8.5px; color: var(--ink); font-family: "Open Sans", sans-serif; font-weight: 600; }

  /* Business cards */
  .card { position: absolute; top: 688px; width: 480px; height: 274px; background: var(--paper); border-radius: 14px; }
  .card--back { left: 88px; }
  .card--front { left: 640px; }
  .card .url { left: 0; right: 0; bottom: 18px; text-align: center; font-size: 15px; color: #222; font-family: "Open Sans", sans-serif; font-weight: 600; }
  .card--back .brand { position: absolute; left: 0; right: 0; top: 150px; justify-content: center; color: var(--navy); font-size: 33px; }
  .card--back .brand__square { width: 26px; height: 26px; background: var(--aqua); }
  .card--front .brand { position: absolute; left: 40px; top: 156px; color: var(--navy); font-size: 20px; gap: 7px; }
  .card--front .brand__square { width: 15px; height: 15px; background: var(--aqua); }
  .card__divider { position: absolute; left: 253px; top: 90px; width: 1px; height: 106px; background: var(--aqua); }
  .holder { position: absolute; left: 279px; top: 86px; color: #222; }
  .holder__name { font-family: "Questrial", sans-serif; font-size: 20px; color: var(--aqua); line-height: 1; }
  .holder__title { font-size: 10px; font-weight: 700; margin-top: 2px; }
  .holder__details { margin-top: 11px; font-size: 10px; font-weight: 700; line-height: 12.5px; }
  .holder__details .contact-line { gap: 5px; }
</style>
</head>
<body>

  <section class="folder">
    <div class="brand"><span class="brand__square"></span>Northgate Renewal</div>
    <div class="url">www.<span class="url__accent">northgate</span>renewalset.example</div>
  </section>

  <section class="letterhead">
    <div class="brand"><span class="brand__square"></span>Northgate Renewal</div>
    <div class="sender">
      <div>42 Unit/3 Albany,</div>
      <div>456, NY</div>
      <div class="contact-line"><svg width="6" height="8" viewBox="0 0 6 8"><rect x="0.5" y="0.5" width="5" height="7" rx="1" fill="none" stroke="#1e2f55"/><rect x="1.5" y="1.5" width="3" height="4" fill="#1e2f55"/></svg>+ 00 000 0000</div>
      <div class="contact-line"><svg width="8" height="7" viewBox="0 0 8 7"><path d="M0 2 Q4 -1 8 2 L7 3 H1 Z M1.5 3.5 H6.5 L7 7 H1 Z" fill="#1e2f55"/></svg>+ 00 000 0000</div>
      <div class="contact-line"><svg width="9" height="6" viewBox="0 0 9 6"><rect width="9" height="6" rx="1" fill="#1e2f55"/><path d="M0.5 0.5 L4.5 3.5 L8.5 0.5" fill="none" stroke="#fff" stroke-width="0.8"/></svg>hello@northgaterenewal.example</div>
    </div>
    <div class="recipient">
      <div>Someone Somebody</div>
      <div>28 Quay Lane</div>
      <div>Perth, Australia</div>
    </div>
    <div class="letter-body">
      <p>Dear Someone Somebody,</p>
      <p>Thank you for reaching out to our team about the options open to you. We have reviewed the notice you shared and prepared a short outline of the next steps, the papers we will need from you and the dates that matter most in the weeks ahead.</p>
      <p>Please gather your recent bank statements, pay slips and any letters from your lender. Bring them to our first meeting so we can build a clear financial picture together.</p>
      <p>Our advisors will work with your attorney to prepare the full package for the court. You will receive a copy of each document before it is filed, along with plain notes on what it means.</p>
      <p>If anything changes with your lender, call us at once. Quick action often keeps more choices open.</p>
      <p>We know this is a hard time, and we are here to help you move forward with a steady plan and a home you can keep. Thank you for trusting us with this step.</p>
      <p>Your Sincerely,<br>Owen Hartley.</p>
    </div>
    <div class="url">www.<span class="url__accent">northgate</span>renewalset.example</div>
  </section>

  <section class="card card--back">
    <div class="brand"><span class="brand__square"></span>Northgate Renewal</div>
    <div class="url">www.<span class="url__accent">northgate</span>renewalset.example</div>
  </section>

  <section class="card card--front">
    <div class="brand"><span class="brand__square"></span>Northgate Renewal</div>
    <div class="card__divider"></div>
    <div class="holder">
      <div class="holder__name">Marcus Delaney</div>
      <div class="holder__title">Title</div>
      <div class="holder__details">
        <div>42 Unit/3 Albany,</div>
        <div>456, NY</div>
        <div class="contact-line"><svg width="8" height="11" viewBox="0 0 8 11"><rect x="0.5" y="0.5" width="7" height="10" rx="1.2" fill="none" stroke="#1e2f55"/><rect x="2" y="2" width="4" height="5.5" fill="#1e2f55"/></svg>+ 00 000 0000</div>
        <div class="contact-line"><svg width="11" height="9" viewBox="0 0 11 9"><path d="M0 3 Q5.5 -1.2 11 3 L9.6 4.2 H1.4 Z M2 4.6 H9 L9.8 9 H1.2 Z" fill="#1e2f55"/></svg>+ 00 000 0000</div>
        <div class="contact-line"><svg width="11" height="8" viewBox="0 0 11 8"><rect width="11" height="8" rx="1" fill="#1e2f55"/><path d="M0.7 0.7 L5.5 4.4 L10.3 0.7" fill="none" stroke="#fff"/></svg>hello@northgaterenewal.example</div>
      </div>
    </div>
    <div class="url">www.<span class="url__accent">northgate</span>renewalset.example</div>
  </section>

</body>
</html>
```